House-share and Room Rental Website (With Focus on the Bedroom Landing Page)

Looking for website design for our House-share (executive accommodation) and room rental business.

Our company name is: Lodgivo could also be written as LodGivo or lodgivo. Either is fine .. just looking for a nice clean catchy logo to go with the design.

EXAMPLES
These are examples of other websites in this field that are doing well. this is a kind of baseline.
https://nestpartners-example.com.au/
https://www.bunkora-example.com/
https://www.dwelzy-example.com/
https://www.habiquo-example.net/
https://www.cohabiscout-example.com.au/

Our business model is to rent rooms to people looking for high-quality accommodation. We fill the gap between those looking to rent rooms and those with rooms to rent. However, our model is slightly different from those already on the market as we looking to fill a massive gap in the market delivering upmarket rooms for rent.(Executive Accommodation) also in the back end will be coupled with a self management process in the back end.

We offer executive style accommodation that stands out above the rest. With special extras like fire safety.. and management processes that create happier homes. We are looking for a web design package that can help us grow and scale our business. We need a design that is captivating

Our MAIN focus is having a room landing page that stands out from the rest... The core of our business will rely on the promotion of the rooms in a share house... so the whole design relies on the BEDROOM landing page to drive results.

Target Market(s)

We have 2 markets we are aiming at ... the first market is people offering rooms to rent who want the highest rental return. The second market is people looking to rent safe, high-quality rooms, in houses that are well managed and looked after.

Industry/Entity Type

Share Economy

Logo Text

LodGivo

Number of Pages Required

5+ page

Font styles to use
Sans Serif

Colors
3276b5

Requirements
Must have
• A messaging system whereby we can create direct communication between those offering rooms and those looking for rooms.
• A call to action that says " Schedule an Inspection"
• Landing page for promoting rooms
• A home page for showing stock.
• Profile page for those selling rooms
• Profile page for those looking for rooms.
• A scheduling calendar for booking inspections
Nice to have
• Pages where new residents can lock in a room.. pay bond and rents.. and sign contracts
• Notifications
• SMS capabilities in the backend.
Should not have
• No script or handwriting fonts.

```html
<!DOCTYPE html>
<html lang="en">
<head>
<meta charset="utf-8">
<title>LodGivo – Room Listing</title>
<link href="https://fonts.googleapis.com/css2?family=Roboto:wght@400;500&family=Roboto+Condensed:wght@400&family=Open+Sans:wght@400&display=swap" rel="stylesheet">
<style>
:root{
  --blue:#2150a8;
  --blue-dark:#1d4aa0;
  --orange:#f57b20;
  --page:#e8e8e8;
  --panel:#ffffff;
  --line:#c8c8c8;
  --ink:#222;
  --muted:#555;
  --value:#2b57b0;
  --footer:#000;
}
*{box-sizing:border-box;margin:0;padding:0}
html,body{width:777px;height:1200px;overflow:hidden}
body{background:var(--page);font-family:"Roboto",sans-serif;color:var(--ink);position:relative}
.abs{position:absolute}

/* header */
.site-header{left:0;top:0;width:777px;height:101px;background:#fff}
.brand{left:58px;top:58px;display:flex;align-items:center;gap:8px;font-family:"Roboto Condensed",sans-serif;font-size:20px;color:var(--ink)}
.brand-mark{width:16px;height:16px;background:var(--orange);border-radius:50%}
.phone{left:482px;top:30px;font-family:"Roboto Condensed",sans-serif;font-size:14px;display:flex;align-items:center;gap:4px}
.cta{left:589px;top:26px;width:130px;height:22px;border-radius:11px;background:var(--blue);color:#fff;font-family:"Roboto Condensed",sans-serif;font-size:11.5px;display:flex;align-items:center;justify-content:center}
.main-nav{left:350px;top:64px;display:flex;gap:0;font-size:11px}
.main-nav a{color:var(--ink);text-decoration:none;margin-right:26px}
.main-nav a:last-child{margin-right:0}
.stripe{top:101px;left:0;width:777px;height:4px;background:linear-gradient(90deg,var(--orange) 50%,var(--blue-dark) 50%)}

/* title card */
.listing-head{left:59px;top:144px;width:662px;height:66px;background:#fff;border:1px solid var(--line)}
.listing-title{left:19px;top:15px;font-family:"Roboto Condensed",sans-serif;font-size:15.5px}
.listing-addr{left:19px;top:39px;font-family:"Roboto Condensed",sans-serif;font-size:11px;color:#333;display:flex;align-items:center;gap:3px}
.price{left:438px;top:20px;font-family:"Roboto Condensed",sans-serif;font-size:15px}
.price small{display:block;font-size:9.5px;color:#444;margin-top:3px;margin-left:-2px}
.owner-btn{left:536px;top:20px;width:109px;height:25px;border-radius:12px;background:var(--orange);color:#fff;font-size:11px;font-weight:500;display:flex;align-items:center;justify-content:center}

/* gallery */
.gallery{left:59px;top:221px;width:355px;height:325px;border:1px solid var(--line);background:#fff}
.ph{position:absolute}
.ph.a{left:1px;top:1px;width:353px;height:150px;background:linear-gradient(135deg,#5c5d5f,#8b7a67 60%,#d9d4cc)}
.ph.b{left:1px;top:153px;width:115px;height:87px;background:linear-gradient(135deg,#8a8b8c,#cfd0d0)}
.ph.c{left:118px;top:153px;width:124px;height:87px;background:linear-gradient(135deg,#e0dcd6,#9b8a76)}
.ph.d{left:244px;top:153px;width:110px;height:87px;background:linear-gradient(135deg,#7a6a5a,#c9b9a4)}
.ph.e{left:1px;top:242px;width:115px;height:82px;background:linear-gradient(135deg,#e8e3dc,#b8865a)}
.ph.f{left:118px;top:242px;width:124px;height:82px;background:linear-gradient(180deg,#6a4c34,#cfcfcf 55%,#7c8d6a)}
.ph.g{left:244px;top:242px;width:110px;height:82px;background:linear-gradient(135deg,#8c8780,#cbc8c2)}

/* features */
.features{left:421px;top:221px;width:299px;height:325px;background:#fff;border:1px solid var(--line)}
.feat{position:absolute;width:135px;height:55px;border:1px solid var(--line);background:#fff}
.feat svg{position:absolute;left:7px;top:15px;width:24px;height:24px}
.feat .v{position:absolute;left:38px;top:9px;font-family:"Roboto Condensed",sans-serif;font-size:14.5px}
.feat .v sub{font-size:8px;vertical-align:baseline}
.feat .k{position:absolute;left:38px;top:31px;font-family:"Roboto Condensed",sans-serif;font-size:10.5px;color:#333}

/* amenities */
.amenities{left:59px;top:557px;width:355px;height:303px;background:#fff;border:1px solid var(--line)}
.panel-title{height:30px;background:#ebebeb;font-size:16px;padding:7px 18px}
.amen-row{position:absolute;left:26px;display:flex;align-items:center;font-size:12px}
.amen-row svg{width:22px;height:22px;margin-right:16px}
.amen-row .lbl{width:163px}
.amen-row .val{color:var(--value)}

/* location */
.location{left:421px;top:557px;width:299px;height:158px;background:#fff;border:1px solid var(--line)}
.map{left:1px;top:1px;width:297px;height:156px;background:linear-gradient(135deg,#f1efe9,#e6e4dc)}
.location .panel-label{left:11px;top:5px;font-size:16px}
.dir-btn{left:223px;top:7px;width:68px;height:13px;border-radius:7px;background:var(--blue);color:#fff;font-size:7.5px;display:flex;align-items:center;justify-content:center}

/* transit */
.transit{left:421px;top:722px;width:299px;height:137px;background:#fff;border:1px solid var(--line)}
.transit .panel-title{height:28px;padding:5px 11px}
.acc{height:36px;border-bottom:1px solid var(--line);display:flex;align-items:center;justify-content:space-between;padding:0 14px 0 17px;font-size:10.5px}
.acc:last-child{border-bottom:none}

/* footer */
.site-footer{left:0;top:916px;width:777px;height:284px;background:var(--footer);color:#fff;font-family:"Open Sans",sans-serif}
.f-head{position:absolute;top:46px;font-family:"Roboto",sans-serif;font-size:12.5px}
.f-contact{position:absolute;left:65px;top:86px;font-size:9px;line-height:14px}
.f-contact .row{display:flex;gap:10px;margin-bottom:9px}
.f-contact svg{width:12px;height:12px;flex:none;margin-top:1px}
.f-links{position:absolute;left:283px;top:85px;font-size:8.5px;list-style:none}
.f-links li{margin-bottom:6px;display:flex;align-items:center;gap:7px}
.f-links li::before{content:"";border-left:3px solid #fff;border-top:2.5px solid transparent;border-bottom:2.5px solid transparent}
.f-social{position:absolute;left:414px;top:84px;font-size:11px}
.f-social .row{display:flex;align-items:center;gap:7px;margin-bottom:12px}
.f-social .dot{width:17px;height:17px;border:1px solid #fff;border-radius:50%}
.f-news{position:absolute;left:539px;top:85px}
.f-news .field{width:174px;height:23px;background:#fff;color:#555;font-size:10px;padding:5px 11px;margin-bottom:5px}
.f-news .send{margin-top:4px;width:78px;height:25px;background:var(--blue);color:#fff;font-size:12px;display:flex;align-items:center;justify-content:center}
.copy{position:absolute;left:0;width:792px;top:232px;text-align:center;font-size:9.5px}
</style>
</head>
<body>

<header class="abs site-header">
  <div class="abs brand"><span class="brand-mark"></span>LodGivo</div>
  <div class="abs phone">
    <svg width="11" height="11" viewBox="0 0 24 24"><path fill="#2150a8" d="M6.6 10.8a15 15 0 0 0 6.6 6.6l2.2-2.2c.3-.3.7-.4 1-.2 1.1.4 2.3.6 3.6.6.6 0 1 .4 1 1V20c0 .6-.4 1-1 1A17 17 0 0 1 3 4c0-.6.4-1 1-1h3.5c.6 0 1 .4 1 1 0 1.3.2 2.5.6 3.6.1.3 0 .7-.2 1z"/></svg>
    1.800.555.0147
  </div>
  <div class="abs cta">Schedule an Inspection</div>
  <nav class="abs main-nav">
    <a href="#">Home</a><a href="#">About us</a><a href="#">Rent Rooms</a><a href="#">Services</a><a href="#">Blog</a><a href="#">Contact Us</a>
  </nav>
</header>
<div class="abs stripe"></div>

<section class="abs listing-head">
  <div class="abs listing-title">Neque porro quisquam est qui dolorem ipsum.</div>
  <div class="abs listing-addr">
    <svg width="11" height="13" viewBox="0 0 24 28"><path d="M12 2a8 8 0 0 0-8 8c0 6 8 15 8 15s8-9 8-15a8 8 0 0 0-8-8z" fill="none" stroke="#333" stroke-width="2"/><circle cx="12" cy="10" r="3" fill="none" stroke="#333" stroke-width="2"/></svg>
    1st Floor, Suite 4, 12 Harbour Lane, Eastbrook WA 6099
  </div>
  <div class="abs price">$ 2,00/M +<small>Non-negotiable</small></div>
  <div class="abs owner-btn">Get Owner Details</div>
</section>

<section class="abs gallery">
  <div class="ph a" role="img" aria-label="Dining room with table, chairs and bookshelves"></div>
  <div class="ph b" role="img" aria-label="Bathroom with freestanding bathtub"></div>
  <div class="ph c" role="img" aria-label="Modern kitchen with island"></div>
  <div class="ph d" role="img" aria-label="Bedroom with double bed"></div>
  <div class="ph e" role="img" aria-label="Study desk with chair"></div>
  <div class="ph f" role="img" aria-label="Covered outdoor patio"></div>
  <div class="ph g" role="img" aria-label="Living room with fireplace and sofa"></div>
</section>

<section class="abs features">
  <div class="feat" style="left:10px;top:11px">
    <svg viewBox="0 0 24 24" fill="none" stroke="#333" stroke-width="1.3"><circle cx="12" cy="7" r="4"/><path d="M4 22v-4c0-3 3-5 8-5s8 2 8 5v4z"/></svg>
    <span class="v">Male</span><span class="k">Gender Preference</span></div>
  <div class="feat" style="left:150px;top:11px">
    <svg viewBox="0 0 24 24" fill="none" stroke="#333" stroke-width="1.3"><path d="M3 12l9-7 9 7M5 11v10h14V11M8 17h8v-3H8z"/></svg>
    <span class="v">550<sub>Sqm</sub></span><span class="k">Size of room</span></div>
  <div class="feat" style="left:10px;top:72px">
    <svg viewBox="0 0 24 24" fill="none" stroke="#333" stroke-width="1.3"><path d="M3 12h18v3a5 5 0 0 1-5 5H8a5 5 0 0 1-5-5zM6 12V5a2 2 0 0 1 4 0M7 20l-1 2M17 20l1 2"/></svg>
    <span class="v">Shared</span><span class="k">Bathroom</span></div>
  <div class="feat" style="left:150px;top:72px">
    <svg viewBox="0 0 24 24" fill="none" stroke="#333" stroke-width="1.5"><rect x="3" y="3" width="18" height="18"/><path d="M9 18V7h4a3 3 0 0 1 0 6H9"/></svg>
    <span class="v">Private</span><span class="k">Parking</span></div>
  <div class="feat" style="left:10px;top:133px">
    <svg viewBox="0 0 24 24" fill="none" stroke="#333" stroke-width="1.3"><circle cx="12" cy="12" r="10"/><path d="M5 5l14 14M6 13h9v2H6z"/></svg>
    <span class="v">non-smoking</span><span class="k">Smoking</span></div>
  <div class="feat" style="left:150px;top:133px">
    <svg viewBox="0 0 24 24" fill="none" stroke="#333" stroke-width="1.3"><path d="M2 20v-8h20v8M2 17h20M4 12V6h16v6M7 12v-3h4v3M13 12v-3h4v3"/></svg>
    <span class="v">76″ X 80″</span><span class="k">Bed size</span></div>
  <div class="feat" style="left:10px;top:193px">
    <svg viewBox="0 0 24 24" fill="none" stroke="#333" stroke-width="1.3"><path d="M3 11l9-8 9 8M5 9v12h14V9M10 21v-6h4v6"/></svg>
    <span class="v">Professionals</span><span class="k">Type of housemates</span></div>
  <div class="feat" style="left:150px;top:193px">
    <svg viewBox="0 0 24 24" fill="none" stroke="#333" stroke-width="1.3"><circle cx="12" cy="6" r="3"/><circle cx="5" cy="16" r="2.5"/><circle cx="19" cy="16" r="2.5"/><path d="M7 10a6 6 0 0 1 10 0M2 22a3 3 0 0 1 6 0M16 22a3 3 0 0 1 6 0"/></svg>
    <span class="v">Shared</span><span class="k">Room type</span></div>
  <div class="feat" style="left:10px;top:256px">
    <svg viewBox="0 0 24 24" fill="none" stroke="#333" stroke-width="1.3"><path d="M2 9a14 14 0 0 1 20 0M5 12.5a9 9 0 0 1 14 0M8.5 16a4 4 0 0 1 7 0"/><circle cx="12" cy="19" r="1"/></svg>
    <span class="v">30<sub>Mbps</sub></span><span class="k">internet speed</span></div>
  <div class="feat" style="left:150px;top:256px">
    <svg viewBox="0 0 24 24" fill="none" stroke="#333" stroke-width="1.3"><path d="M5 2h10l4 4v16H5zM8 9h8M8 12h8M8 15h8M8 18h6"/></svg>
    <span class="v">3 months</span><span class="k">minimum contract..</span></div>
</section>

<section class="abs amenities">
  <div class="panel-title">Amenities</div>
  <div class="amen-row" style="top:50px"><svg viewBox="0 0 24 24" fill="none" stroke="#333" stroke-width="1.3"><rect x="6" y="2" width="12" height="8"/><path d="M4 12h16M12 12v6M7 22l5-4 5 4"/></svg><span class="lbl">Furnishing Status</span><span class="val">Full</span></div>
  <div class="amen-row" style="top:84px"><svg viewBox="0 0 24 24" fill="none" stroke="#333" stroke-width="1.3"><rect x="3" y="4" width="18" height="12"/><path d="M9 20h6M12 16v4"/></svg><span class="lbl">TV</span><span class="val">Yes</span></div>
  <div class="amen-row" style="top:118px"><svg viewBox="0 0 24 24" fill="none" stroke="#333" stroke-width="1.3"><path d="M3 11l9-8 9 8M5 9v12h14V9M10 21v-5h4v5"/></svg><span class="lbl">Storage space</span><span class="val">Yes</span></div>
  <div class="amen-row" style="top:152px"><svg viewBox="0 0 24 24" fill="none" stroke="#333" stroke-width="1.3"><path d="M2 12h20M4 12v10M20 12v10M10 12v-3h6v3M6 2l2 6"/></svg><span class="lbl">Study Desk</span><span class="val">NA</span></div>
  <div class="amen-row" style="top:186px"><svg viewBox="0 0 24 24" fill="none" stroke="#333" stroke-width="1.3"><path d="M12 7a2 2 0 1 1 2-2M12 7v3L2 17h20L12 10"/></svg><span class="lbl">Wardrobe</span><span class="val">NA</span></div>
  <div class="amen-row" style="top:220px"><svg viewBox="0 0 24 24" fill="none" stroke="#333" stroke-width="1.3"><path d="M20 3v6M20 5h-6l-3 3H5v3h12V8M6 14v1M9 14v1M12 14v1M15 14v1M6 18v1M9 18v1M12 18v1M15 18v1"/></svg><span class="lbl">Ensuite shower</span><span class="val">Yes</span></div>
  <div class="amen-row" style="top:254px"><svg viewBox="0 0 24 24" fill="none" stroke="#333" stroke-width="1.3"><path d="M8 2v20M6 2v6a2 2 0 0 0 4 0V2M15 22V2c3 0 3 8 0 9"/></svg><span class="lbl">Kitchenette</span><span class="val">yes</span></div>
</section>

<section class="abs location">
  <div class="abs map" role="img" aria-label="Map showing the room location"></div>
  <div class="abs panel-label">Location</div>
  <div class="abs dir-btn">Get Directions</div>
  <svg class="abs" style="left:147px;top:63px" width="10" height="14" viewBox="0 0 24 32"><path d="M12 0a10 10 0 0 0-10 10c0 8 10 22 10 22s10-14 10-22A10 10 0 0 0 12 0z" fill="#e02020"/></svg>
</section>

<section class="abs transit">
  <div class="panel-title">Transit</div>
  <div class="acc">Bus Stops<svg width="10" height="7" viewBox="0 0 10 7"><path d="M1 1l4 4 4-4" fill="none" stroke="#222" stroke-width="1.8"/></svg></div>
  <div class="acc">Railway Station<svg width="10" height="7" viewBox="0 0 10 7"><path d="M1 1l4 4 4-4" fill="none" stroke="#222" stroke-width="1.8"/></svg></div>
  <div class="acc">Metro Station<svg width="10" height="7" viewBox="0 0 10 7"><path d="M1 1l4 4 4-4" fill="none" stroke="#222" stroke-width="1.8"/></svg></div>
</section>

<footer class="abs site-footer">
  <div class="f-head" style="left:65px">CONTACT US</div>
  <div class="f-head" style="left:279px">QUICK LINKS</div>
  <div class="f-head" style="left:413px">FOLLOW US</div>
  <div class="f-head" style="left:539px">NEWSLETTER</div>

  <div class="f-contact">
    <div class="row"><svg viewBox="0 0 24 24"><path fill="#fff" d="M12 1a8 8 0 0 0-8 8c0 6 8 14 8 14s8-8 8-14a8 8 0 0 0-8-8zm0 11a3 3 0 1 1 0-6 3 3 0 0 1 0 6z"/></svg><span>1st Floor, Suite 4, 12 Harbour<br>Lane, Eastbrook WA 6099</span></div>
    <div class="row"><svg viewBox="0 0 24 24"><path fill="#fff" d="M6.6 10.8a15 15 0 0 0 6.6 6.6l2.2-2.2c.3-.3.7-.4 1-.2 1.1.4 2.3.6 3.6.6.6 0 1 .4 1 1V20c0 .6-.4 1-1 1A17 17 0 0 1 3 4c0-.6.4-1 1-1h3.5c.6 0 1 .4 1 1 0 1.3.2 2.5.6 3.6.1.3 0 .7-.2 1z"/></svg><span>+61 8 5550 2100</span></div>
    <div class="row"><svg viewBox="0 0 24 24"><path fill="#fff" d="M2 5h20v14H2zm2 2v1l8 5 8-5V7l-8 5z"/></svg><span>hello@lodgivo-example.com</span></div>
  </div>

  <ul class="f-links">
    <li>Home</li><li>About us</li><li>Products</li><li>News</li><li>Contact</li>
  </ul>

  <div class="f-social">
    <div class="row"><span class="dot"></span>Friendly</div>
    <div class="row"><span class="dot"></span>Snapgram</div>
    <div class="row" style="font-size:9px"><span class="dot"></span>Circleplus</div>
  </div>

  <div class="f-news">
    <div class="field">Your Name</div>
    <div class="field">Email address</div>
    <div class="send">SEND</div>
  </div>

  <div class="copy">© Copyright 2019 . All Rights Reserved.</div>
</footer>

</body>
</html>
```